Dunmore Roofing

Want a professional looking business card

Industry/Entity Type

Business

Contact Information for Business Card

Paul Dunmore ( Owner) paul@dunmoreroofing-example.com, www.dunmoreroofing-example.com, Adress: 4172 Township road 43 Plantagenet,ON K9X4T2

```html
<!DOCTYPE html>
<html lang="en">
<head>
<meta charset="utf-8">
<title>Dunmore Roofing – Business Card</title>
<link href="https://fonts.googleapis.com/css2?family=Roboto:wght@400;500;700&display=swap" rel="stylesheet">
<style>
  :root {
    --brand-blue: #1b4585;
    --card-white: #ffffff;
    --accent-grey: #8a8c8f;
    --backdrop: #e9e6e1;
    --text-light: #ffffff;
  }
  * { margin: 0; padding: 0; box-sizing: border-box; }
  html, body {
    width: 1200px;
    height: 902px;
    overflow: hidden;
    background: var(--backdrop);
    font-family: "Roboto", Arial, sans-serif;
  }
  .stage {
    position: relative;
    width: 1200px;
    height: 902px;
  }
  .business-card {
    position: absolute;
    left: 100px;
    top: 165px;
    width: 1000px;
    height: 572px;
    border-radius: 30px;
    overflow: hidden;
    background: var(--card-white);
    box-shadow: 0 6px 24px rgba(0,0,0,0.12);
  }
  .card-shapes {
    position: absolute;
    inset: 0;
  }
  .contact-panel {
    position: absolute;
    left: 50px;
    top: 0;
    color: var(--text-light);
  }
  .owner-name {
    position: absolute;
    top: 96px;
    left: 0;
    font-size: 34px;
    font-weight: 500;
    white-space: nowrap;
    line-height: 1;
  }
  .owner-title {
    position: absolute;
    top: 132px;
    left: 0;
    font-size: 24px;
    font-weight: 400;
    line-height: 1;
  }
  .address {
    position: absolute;
    top: 288px;
    left: 2px;
    font-size: 25px;
    font-style: normal;
    line-height: 34px;
    white-space: nowrap;
  }
  .contact-list {
    position: absolute;
    top: 380px;
    left: 0;
    list-style: none;
  }
  .contact-item {
    display: flex;
    align-items: center;
    height: 34px;
    font-size: 23px;
    white-space: nowrap;
  }
  .contact-icon {
    width: 28px;
    height: 28px;
    margin-right: 8px;
    flex: none;
  }
  .brand-name {
    position: absolute;
    left: 500px;
    width: 490px;
    top: 266px;
    text-align: center;
    color: var(--brand-blue);
    font-size: 40px;
    font-weight: 700;
    letter-spacing: 1px;
    text-transform: uppercase;
    line-height: 1;
    white-space: nowrap;
  }
</style>
</head>
<body>
<main class="stage">
  <section class="business-card" aria-label="Dunmore Roofing business card">
    <svg class="card-shapes" viewBox="0 0 1000 572" width="1000" height="572" aria-hidden="true">
      <path d="M0 0 H518 Q387 286 516 572 H0 Z" fill="var(--brand-blue)"/>
      <path d="M526 0 Q391 286 532 572 L536 572 Q403 286 530 0 Z" fill="var(--accent-grey)"/>
    </svg>

    <div class="contact-panel">
      <h1 class="owner-name">Paul Dunmore</h1>
      <p class="owner-title">Owner</p>

      <address class="address">4172 Township road 43,<br>Harlow Bend, NR K9X4T2</address>

      <ul class="contact-list">
        <li class="contact-item">
          <svg class="contact-icon" viewBox="0 0 28 28" aria-hidden="true">
            <circle cx="14" cy="14" r="12.5" fill="none" stroke="#fff" stroke-width="2"/>
            <path d="M8 11 Q14 7 20 11 L19 13 L17 12 L16 10 H12 L11 12 L9 13 Z" fill="#fff"/>
            <rect x="9" y="14" width="10" height="6" rx="1.5" fill="#fff"/>
          </svg>
          <span>(555) 201-0142</span>
        </li>
        <li class="contact-item">
          <svg class="contact-icon" viewBox="0 0 28 28" aria-hidden="true">
            <circle cx="14" cy="14" r="12.5" fill="none" stroke="#fff" stroke-width="2"/>
            <rect x="7.5" y="9.5" width="13" height="9" fill="#fff"/>
            <path d="M7.5 9.5 L14 15 L20.5 9.5 M7.5 18.5 L12 14 M20.5 18.5 L16 14" fill="none" stroke="var(--brand-blue)" stroke-width="1.2"/>
          </svg>
          <span>paul@dunmoreroofing-example.com</span>
        </li>
        <li class="contact-item">
          <svg class="contact-icon" viewBox="0 0 28 28" aria-hidden="true">
            <circle cx="14" cy="14" r="12.5" fill="none" stroke="#fff" stroke-width="2"/>
            <circle cx="14" cy="14" r="7" fill="none" stroke="#fff" stroke-width="1.4"/>
            <ellipse cx="14" cy="14" rx="3" ry="7" fill="none" stroke="#fff" stroke-width="1.2"/>
            <path d="M7 14 H21 M8.5 10.5 H19.5 M8.5 17.5 H19.5" stroke="#fff" stroke-width="1.1"/>
          </svg>
          <span>www.dunmoreroofing-example.com</span>
        </li>
      </ul>
    </div>

    <p class="brand-name">Dunmore Roofing</p>
  </section>
</main>
</body>
</html>
```